Women's Jewellery startup needs a captivating, beautifully designed and intuitive online store

[12/24 update]

Added 2 additional documents:

Feedback on designs received so far: designer feedback.docx
Product images from catalogue: products images.docx

Please read the feedback provided on designs provided so far to guide you further on your submission. The product images can be used to create promotional banners for the site.

@@@Added a document (VELISTO JEWELLERY_checklist.docx) which can be used by designers as a checklist when submitting their designs to ensure all aspects of the requirements have been covered @@@

+++IMPORTANT BUT NOT SPECIFIED IN THE REQUIREMENTS DOCUMENT - DESIGN SHOULD INCLUDE SUPPORT FOR MOBILE FRIENDLY SITE TOO+++

***Previous experience designing Jewellery online stores preferred (not essential)***

The name of the online Jewellery store is "Velisto Jewellery" and the business is based in Hong Kong. It will be run by 2 stay at home mothers. We need a Shopify themed store designed that will achieve the following objectives in order of priority:

• Conversion: The primary objective of the design/content is to prompt the customer to make a purchase. While this may sound obvious, it is mentioned so as not to distract the design process by focusing on other objectives (which are also important). The site also needs to be optimized so as to rank high in search engine searches for relevant keywords (SEO)
• Navigation: An intuitive interface which takes away a lot of the thinking from the customer by making it obvious what they need to do when they visit the store
• Engagement: Encourages the customer to spend time on the website and share content with their social network

Where applicable, the design of the store should reflect as closely as possible the mission statements and words outlined below:

• Jewellery you’ll fall in love with
• We want every client to leave the store with a smile
• We want to be able to provide the best service we can in every situation no matter what
• We aim to increase our business by word of mouth; therefore we tell people things about our store that makes it interesting for them to share
• We love every customer, no matter how difficult things get
• We, as a team, are so well informed about our products and brands that we always have the best information for our customers
• We celebrate women here!
• We celebrate life in here!
• We celebrate beauty here!
• We celebrate families here, as jewellery often stays within families.
• We will always try to make an extra step
• We will always try to exceed the expectation of our customers
• We will go as far as we possibly can to attract a customer back to our store and connect with us
• Every client that leaves our store knows more about jewellery because we passionately told him about it
• Romantic, classic, love, warm, cool, stylish

A draft functional specification is attached with this brief. We would like the design to reflect as closely as possible the functional requirements outlined in the document. Open to suggestions to improve upon the functional requirements.

Target Market(s)

Women aged 18-55

Industry/Entity Type

Jewelry Store

Coding

Coded - Design and coding required

Number of Pages Required

5+ page

Font styles to use
Other font styles liked:
• Myriad Pro as per Logo but open to any font that complements this one

Requirements
Must have
• 1. A look that encourages the user to make a purchase
• 2. An intuitive, easy to navigate and engaging interface
• 3. Primary colour scheme as defined in the functional specification attached
• 4. Simplistic look, not too cluttered
Nice to have
• 1. Closely matching the functional requirements of the site as outlined in the requirements specification but open to any better ideas

```html
<!DOCTYPE html>
<html lang="en">
<head>
<meta charset="utf-8">
<title>Velisto Jewellery</title>
<link rel="stylesheet" href="https://fonts.googleapis.com/css2?family=Montserrat:wght@400;500;600;700&display=swap">
<style>
:root{
  --black:#000;
  --ink:#111;
  --gold:#c9a24a;
  --gold-soft:#d9b867;
  --white:#fff;
  --grey:#9a9a9a;
  --red-deep:#6e0410;
  --red:#c0111e;
  --pearl:#f4eee6;
}
*{box-sizing:border-box;margin:0;padding:0}
html,body{width:1200px;height:2340px;overflow:hidden;background:var(--white)}
body{position:relative;font-family:"Montserrat",Arial,sans-serif;color:var(--ink)}
.site-header{position:absolute;left:0;top:0;width:1200px;height:248px;background:var(--black)}
.menu-toggle{position:absolute;left:28px;top:12px}
.header-tools{position:absolute;right:24px;top:12px;display:flex;gap:24px}
.brand{position:absolute;left:0;top:44px;width:1200px;text-align:center;color:var(--gold)}
.brand-mark{width:34px;height:34px;border:2px solid var(--gold);border-radius:50%;margin:0 auto 14px}
.brand-name{font-size:40px;font-weight:600;letter-spacing:10px}
.brand-tagline{font-size:13px;letter-spacing:2.5px;margin-top:6px;font-weight:500}
.main-nav{position:absolute;left:0;top:214px;width:1200px;display:flex;justify-content:center;gap:46px;font-size:12px;font-weight:600;letter-spacing:1px;color:var(--white)}
.main-nav .active{border-bottom:2px solid var(--white);padding-bottom:4px}

.hero{position:absolute;left:0;top:248px;width:1200px;height:504px;
  background:
    radial-gradient(ellipse 300px 230px at 250px 250px,var(--pearl) 0%,#e7d9c9 40%,rgba(200,160,140,.55) 70%,rgba(160,30,40,0) 100%),
    radial-gradient(ellipse 420px 300px at 180px 240px,rgba(150,90,80,.7) 0%,rgba(120,20,30,0) 100%),
    linear-gradient(160deg,#9c0a18 0%,var(--red) 45%,#a00c19 70%,var(--red-deep) 100%)}
.hero-copy{position:absolute;left:688px;top:164px;color:var(--white)}
.hero-copy h1{font-size:16px;font-weight:700;letter-spacing:1px}
.btn{display:inline-block;background:var(--white);color:var(--ink);font-size:10px;font-weight:700;letter-spacing:1px;padding:12px 30px}
.hero-copy .btn{margin-top:36px}

.section-title{position:absolute;left:0;top:802px;width:1200px;text-align:center;font-size:22px;font-weight:500;letter-spacing:1px}
.card{position:absolute;overflow:hidden}
.card-men{left:112px;top:860px;width:480px;height:340px;
  background:
    radial-gradient(ellipse 150px 120px at 240px 205px,#f6dc8a 0%,#d9ad45 45%,rgba(201,162,74,0) 100%),
    linear-gradient(135deg,#eceef6 0%,#cfd3e6 55%,#b9bfd8 100%)}
.card-vintage{left:608px;top:860px;width:480px;height:340px;
  background:
    radial-gradient(circle at 240px 195px,#9b1526 0%,#6e0a18 16%,#d8d8d8 22%,#9a9a9a 34%,rgba(60,60,60,0) 55%),
    linear-gradient(180deg,#3a3a3a 0%,#1a1a1a 100%)}
.card-label{position:absolute;top:22px;width:100%;text-align:center;font-size:15px;font-weight:600;letter-spacing:1px}
.card-men .card-label{color:var(--ink)}
.card-vintage .card-label{color:var(--white)}

.card-bride{left:112px;top:1220px;width:976px;height:396px;
  background:
    radial-gradient(ellipse 170px 200px at 660px 150px,#bdbdbd 0%,rgba(120,120,120,0) 100%),
    radial-gradient(ellipse 220px 170px at 800px 330px,#e6e6e6 0%,#a8a8a8 50%,rgba(90,90,90,0) 100%),
    linear-gradient(90deg,#151515 0%,#151515 45%,#4a4a4a 62%,#8c8c8c 85%,#6e6e6e 100%)}
.card-copy{position:absolute;font-size:15px;font-weight:700;letter-spacing:.5px}
.card-copy p{font-size:11px;font-weight:500;margin-top:8px}
.card-copy .btn{margin-top:22px;padding:10px 22px}
.card-bride .card-copy{left:52px;top:62px;color:var(--white)}

.card-collection{left:112px;top:1632px;width:976px;height:400px;
  background:
    radial-gradient(ellipse 230px 190px at 190px 200px,#ffe08a 0%,#d7a331 40%,#9a6c14 70%,rgba(154,108,20,0) 100%),
    linear-gradient(90deg,#8a6412 0%,#d4ab4f 35%,#f0d99a 60%,#fbf0d4 100%)}
.card-collection .card-copy{left:508px;top:200px;color:var(--ink)}

.site-footer{position:absolute;left:0;top:2060px;width:1200px;height:280px;background:var(--black);color:var(--white)}
.footer-col{position:absolute;top:24px;font-size:10px;line-height:19px;color:#cfcfcf}
.footer-col h3{font-size:13px;font-weight:700;color:var(--white);letter-spacing:.5px;margin-bottom:8px}
.col-about{left:112px}.col-shopping{left:300px}.col-care{left:448px}.col-news{left:688px;width:400px}
.newsletter-form{display:flex;margin-top:16px}
.newsletter-form span{flex:1;background:var(--white);color:var(--grey);padding:8px 10px;font-size:10px}
.newsletter-form b{background:var(--gold);color:var(--white);padding:8px 18px;font-size:10px}
.social{position:absolute;left:112px;top:228px;display:flex;gap:10px}
.social i{width:22px;height:22px;border-radius:50%;background:var(--gold-soft)}
.legal{position:absolute;right:112px;top:232px;font-size:10px;color:#cfcfcf}
.legal u{margin-left:16px;color:var(--white)}
</style>
</head>
<body>
<header class="site-header">
  <svg class="menu-toggle" width="20" height="16" viewBox="0 0 20 16"><g stroke="#fff" stroke-width="2"><line x1="0" y1="2" x2="20" y2="2"/><line x1="0" y1="8" x2="20" y2="8"/><line x1="0" y1="14" x2="20" y2="14"/></g></svg>
  <div class="header-tools">
    <svg width="16" height="16" viewBox="0 0 16 16"><circle cx="6.5" cy="6.5" r="5" fill="none" stroke="#fff" stroke-width="2"/><line x1="10" y1="10" x2="15" y2="15" stroke="#fff" stroke-width="2"/></svg>
    <svg width="16" height="16" viewBox="0 0 16 16"><line x1="2" y1="14" x2="14" y2="2" stroke="#fff" stroke-width="2"/></svg>
    <svg width="16" height="16" viewBox="0 0 16 16"><circle cx="8" cy="5" r="4" fill="#fff"/><path d="M1 16c0-5 14-5 14 0z" fill="#fff"/></svg>
    <svg width="16" height="16" viewBox="0 0 16 16"><path d="M8 15L1.5 8.5A4 4 0 018 3a4 4 0 016.5 5.5z" fill="#fff"/></svg>
    <svg width="16" height="16" viewBox="0 0 16 16"><rect x="2" y="5" width="12" height="10" fill="#fff"/><path d="M5 5a3 3 0 016 0" fill="none" stroke="#fff" stroke-width="2"/></svg>
  </div>
  <div class="brand">
    <div class="brand-mark"></div>
    <div class="brand-name">VELISTO</div>
    <div class="brand-tagline">JEWELLERY YOU'LL FALL IN LOVE WITH</div>
  </div>
  <nav class="main-nav">
    <span class="active">ABOUT US</span><span>WOMEN</span><span>MEN</span><span>ENGAGEMENT</span><span>VELISTO COLLECTIONS</span><span>GIFT</span>
  </nav>
</header>

<section class="hero" role="img" aria-label="Pearls spilling from an open seashell onto red silk">
  <div class="hero-copy">
    <h1>KNOW YOUR WORTH, YOU ARE PRICELESS!</h1>
    <span class="btn">DISCOVER</span>
  </div>
</section>

<h2 class="section-title">OUR COLLECTIONS</h2>

<div class="card card-men" role="img" aria-label="Gold signet ring on a pale blue background">
  <div class="card-label">MEN</div>
</div>
<div class="card card-vintage" role="img" aria-label="Vintage ruby and diamond cluster ring on dark grey">
  <div class="card-label">VINTAGE</div>
</div>

<div class="card card-bride" role="img" aria-label="Black and white photograph of a bride in lace">
  <div class="card-copy">SHINE ON THE BRIDE<p>EXPLORE OUR BRIDAL COLLECTION</p><span class="btn">EXPLORE</span></div>
</div>

<div class="card card-collection" role="img" aria-label="Gold-plated rose jewellery piece on a golden background">
  <div class="card-copy">VELISTO COLLECTION<br><span class="btn">EXPLORE</span></div>
</div>

<footer class="site-footer">
  <div class="footer-col col-about"><h3>ABOUT US</h3>Our Story<br>Wholesale Enquiries</div>
  <div class="footer-col col-shopping"><h3>SHOPPING</h3>Shipping<br>Refund Policy<br>Returns<br>Size Guide</div>
  <div class="footer-col col-care"><h3>CUSTOMER CARE</h3>Returns<br>FAQs<br>Care &amp; Warranty<br>Contact Us</div>
  <div class="footer-col col-news"><h3>NEWSLETTER SIGNUP</h3>Join our list for new arrivals, private offers and gift ideas for the ones you love.
    <div class="newsletter-form"><span>Enter email address</span><b>SUBSCRIBE</b></div>
  </div>
  <div class="social"><i></i><i></i><i></i><i></i></div>
  <div class="legal">© All Rights Reserved <u>TERMS &amp; CONDITIONS</u></div>
</footer>
</body>
</html>
```